VelkaVision.com

Complete Website Design (Godaddy) and company Branding / Logo Design. The products will sell are only done in-person and are installed. So this site does not need to be an e-commerce site. We will only be giving out information and collecting customer inquires. Website will only need to be about 3 to 5 pages.

```html
<!DOCTYPE html>
<html lang="en">
<head>
<meta charset="utf-8">
<title>Velka Vision — TV Installation</title>
<link rel="stylesheet" href="https://fonts.googleapis.com/css2?family=Lexend+Exa:wght@500;600;700&family=Poppins:wght@400;500&display=swap">
<style>
:root{
  --gold:#d19a2a;
  --gold-light:#e2b02f;
  --ink:#1c1c1c;
  --text:#2a2a2a;
  --grey:#9a9a9a;
  --line:#e3e3e3;
  --white:#ffffff;
}
*{margin:0;padding:0;box-sizing:border-box}
html,body{width:1200px;height:2516px;overflow:hidden;background:var(--white)}
body{position:relative;font-family:'Poppins',sans-serif;color:var(--text)}
.abs{position:absolute}
.display{font-family:'Lexend Exa',sans-serif;text-transform:uppercase}

/* header */
.site-header{top:0;left:0;width:1200px;height:95px;box-shadow:0 2px 4px rgba(0,0,0,.06);background:var(--white);z-index:3}
.brand{left:75px;top:30px;font-size:31px;font-weight:600;color:var(--ink);letter-spacing:1px}
.main-nav{right:47px;top:42px;display:flex;gap:35px;font-size:14.5px;font-weight:500;letter-spacing:.5px}
.main-nav a{color:var(--ink);text-decoration:none}
.main-nav a.active{color:var(--gold)}

/* hero */
.hero{top:95px;left:0;width:1200px;height:665px;
  background:linear-gradient(100deg,#b9b6b9 0%,#8a8489 30%,#4a4a5a 50%,#556a9c 62%,#9c9aa6 85%,#c3c0c4 100%);
  clip-path:polygon(0 0,1200px 0,1200px 633px,960px 665px,600px 617px,240px 665px,0 635px)}
.hero-shade{top:0;left:0;width:100%;height:100%;background:rgba(0,0,0,.18)}
.hero-text{left:0;width:1200px;text-align:center;color:var(--white)}
.hero-kicker{top:183px;font-size:45px;font-weight:700;letter-spacing:2px}
.hero-title{top:230px;font-size:70px;font-weight:700;letter-spacing:2px;line-height:1}
.hero-sub{top:318px;font-size:21px;font-weight:600;line-height:32px;letter-spacing:.5px}
.btn{display:flex;align-items:center;justify-content:center;color:var(--white);font-family:'Lexend Exa',sans-serif;font-weight:600;text-transform:uppercase;letter-spacing:1px}
.hero-btn{left:512px;top:399px;width:178px;height:51px;background:var(--gold);font-size:14.5px}
.arrow{top:277px}

/* about */
.about-accent-gold{left:502px;top:825px;width:99px;height:89px;background:var(--gold)}
.about-accent-dark{left:60px;top:1070px;width:180px;height:164px;background:var(--ink)}
.about-photo{left:75px;top:841px;width:512px;height:375px;background:linear-gradient(90deg,#3a4a57 0%,#8fa2ae 38%,#e8e6e3 55%,#5a6fb3 75%,#dcd8d2 100%)}
.about-title{left:615px;top:852px;font-size:34px;font-weight:700;color:var(--ink);letter-spacing:1px}
.about-title span{color:var(--gold)}
.rule{height:3px}
.about-rule{left:615px;top:923px;width:125px;background:var(--grey)}
.about-copy{left:615px;top:958px;width:515px;font-size:15px;line-height:27px;color:var(--text)}
.about-btn{left:615px;top:1147px;width:178px;height:50px;background:var(--gold);font-size:14.5px}

/* contact */
.contact-band{top:1310px;left:0;width:1200px;height:778px;
  background:linear-gradient(115deg,#c3832a 0%,#d99c2b 35%,#e3ad30 60%,#c98a2a 85%,#d9a22e 100%);
  clip-path:polygon(0 0,212px 0,600px 53px,990px 0,1200px 0,1200px 695px,600px 777px,0 695px)}
.contact-title{left:0;width:1200px;top:1422px;text-align:center;font-size:34px;font-weight:700;color:var(--white);letter-spacing:1px}
.contact-rule{left:538px;top:1490px;width:124px;background:var(--white)}
.field{background:var(--white);font-size:13.5px;color:#444;padding:0 19px;display:flex;align-items:center;text-transform:uppercase}
.field.col-a{left:254px;width:333px}
.field.col-b{left:616px;width:333px}
.field.row-1{top:1540px;height:56px}
.field.row-2{top:1614px;height:56px}
.field.row-3{top:1686px;height:56px}
.field.message{left:254px;width:695px;top:1760px;height:136px;align-items:flex-start;padding-top:22px}
.submit-btn{left:499px;top:1924px;width:206px;height:50px;background:var(--ink);font-size:16px}

/* footer */
.footer-col{top:2160px}
.footer-col h4{font-family:'Lexend Exa',sans-serif;font-weight:600;font-size:19px;color:var(--ink);letter-spacing:1px;text-transform:uppercase;margin-bottom:10px}
.footer-col li{list-style:none;font-size:17px;color:var(--text);line-height:34.5px}
.col-sitemap{left:74px}
.col-sitemap li{line-height:34px}
.col-products{left:318px}
.col-products li{line-height:37px}
.col-services{left:604px}
.col-contact{left:855px}
.contact-item{display:flex;gap:16px;font-size:17px;line-height:26px;margin-bottom:11px}
.contact-item svg{flex:none;margin-top:5px}
.socials{display:flex;gap:20px;margin-top:22px}
.socials span{width:24px;height:24px;border-radius:50%;background:var(--ink)}
.footer-line{left:0;top:2447px;width:1200px;height:1px;background:var(--line)}
.copyright{left:0;width:1200px;top:2471px;text-align:center;font-size:14px;color:var(--text)}
</style>
</head>
<body>

<header class="site-header abs">
  <div class="brand display abs">Velka Vision</div>
  <nav class="main-nav display abs">
    <a class="active" href="#">Home</a>
    <a href="#">About</a>
    <a href="#">Services</a>
    <a href="#">Products</a>
    <a href="#">Contact</a>
  </nav>
</header>

<section class="hero abs" role="img" aria-label="Technician in blue overalls installing a flat screen TV on a white living room media unit">
  <div class="hero-shade abs"></div>
  <svg class="arrow abs" style="left:60px" width="26" height="44" viewBox="0 0 26 44"><path d="M23 2 L3 22 L23 42" fill="none" stroke="#fff" stroke-width="2.5"/></svg>
  <svg class="arrow abs" style="left:1114px" width="26" height="44" viewBox="0 0 26 44"><path d="M3 2 L23 22 L3 42" fill="none" stroke="#fff" stroke-width="2.5"/></svg>
  <div class="hero-text hero-kicker display abs">Welcome to</div>
  <div class="hero-text hero-title display abs">Velka Vision</div>
  <div class="hero-text hero-sub display abs">Quis autem vel eum iure reprehenderit qui in ea<br>voluptate velit esse quam nihil .</div>
  <a class="btn hero-btn abs">Contact Us</a>
</section>

<section class="about">
  <div class="about-accent-gold abs"></div>
  <div class="about-accent-dark abs"></div>
  <div class="about-photo abs" role="img" aria-label="Smiling technician in blue cap and overalls holding a clipboard beside a flat screen TV"></div>
  <h2 class="about-title display abs">About <span>Velka Vision</span></h2>
  <div class="rule about-rule abs"></div>
  <p class="about-copy abs">Nemo enim ipsam voluptatem quia voluptas sit aspernatur aut odit aut fugit, sed quia consequuntur magni dolores eos qui ratione voluptatem sequi nesciunt. Neque porro quisquam est, qui dolorem ipsum quia dolor sit amet, consectetur, adipisci velit, sed quia non numquam eius modi tempora incidunt ut labore et dolore magnam aliquam quaerat voluptatem.</p>
  <a class="btn about-btn abs">Read More</a>
</section>

<section class="contact">
  <div class="contact-band abs" role="img" aria-label="Wall mount brackets and installation tools on a yellow background"></div>
  <h2 class="contact-title display abs">Contact Us</h2>
  <div class="rule contact-rule abs"></div>
  <div class="field col-a row-1 abs">First Name</div>
  <div class="field col-b row-1 abs">Last Name</div>
  <div class="field col-a row-2 abs">Company</div>
  <div class="field col-b row-2 abs">Email</div>
  <div class="field col-a row-3 abs">Telephone</div>
  <div class="field col-b row-3 abs">Subject</div>
  <div class="field message abs">Message</div>
  <a class="btn submit-btn abs">Submit</a>
</section>

<footer>
  <div class="footer-col col-sitemap abs">
    <h4>Site Map</h4>
    <ul><li>Home</li><li>About</li><li>Services</li><li>Products</li><li>Contact</li></ul>
  </div>
  <div class="footer-col col-products abs">
    <h4>Products</h4>
    <ul><li>Sed ut perspiciatis</li><li>Unde omnis iste</li><li>Natus error</li><li>Sit voluptatemac</li><li>Cusantium</li></ul>
  </div>
  <div class="footer-col col-services abs">
    <h4>Services</h4>
    <ul><li>Nemo enim ipsam</li><li>voluptatem</li><li>Quia voluptas sit</li><li>aspernatur</li><li>Aut odit aut</li></ul>
  </div>
  <div class="footer-col col-contact abs">
    <h4>Contact Us</h4>
    <div class="contact-item">
      <svg width="18" height="16" viewBox="0 0 18 16"><path d="M1 3 L6 1 L12 3 L17 1 L17 13 L12 15 L6 13 L1 15 Z" fill="#d19a2a"/></svg>
      <span>48 Harlow Lane Suite 210,<br>Denver 80203,<br>United States</span>
    </div>
    <div class="contact-item">
      <svg width="18" height="16" viewBox="0 0 18 16"><path d="M4 1 L7 4 L5 6 Q7 10 10 11 L12 9 L15 12 L12 15 Q3 13 1 4 Z" fill="#d19a2a"/></svg>
      <span>+1 555-014-2290</span>
    </div>
    <div class="contact-item">
      <svg width="18" height="16" viewBox="0 0 18 16"><rect x="1" y="3" width="16" height="11" fill="#d19a2a"/><path d="M1 3 L9 9 L17 3" fill="none" stroke="#fff" stroke-width="1.3"/></svg>
      <span>hello@velkavision.com</span>
    </div>
    <div class="socials" aria-label="Social media links">
      <span></span><span></span><span></span><span></span><span></span>
    </div>
  </div>
  <div class="footer-line abs"></div>
  <p class="copyright abs">Copyright ©2024 by Velka Vision. All Right Reserved</p>
</footer>

</body>
</html>
```